Stylish Business Cards Wanted

- DOUBLE SIDED Design Required -

High end, edgy cards for a corporate and personal stylist. Must include logo,
Name: Belinda Harwick
Title: Director and Stylist
telephone : +61 8 7142 5809
email: belinda@theloombriefing.example
website: theloombriefing.example
Tag: Corporate Workwear & Uniform Specialist | Personal Stylist
Would like nice icons for telephone, email, website

Target Market(s)

Businesses wanting stylish uniforms, people wanting stylish wardrobes

Industry/Entity Type

Corporate Workwear Stylist

Contact Information for Business Card

I would like black, white and gold foiling incorporated in the design - possibly a touch of the other colours on my branding guide attached Name: Belinda Harwick Title: Director and Stylist telephone : +61 8 7142 5809 email: belinda@theloombriefing.example website: theloombriefing.example Tag: Corporate Workwear & Uniform Specialist | Personal Stylist Would like nice icons for telephone, email, website

Font styles to use
Other font styles liked:
• Raleway

Colors

Designer to choose colors to be used in the design.

Requirements
Must have
• Gold foil accents

```html
<!DOCTYPE html>
<html lang="en">
<head>
<meta charset="utf-8">
<title>The Loom Briefing – Business Cards</title>
<link rel="stylesheet" href="https://fonts.googleapis.com/css2?family=Raleway:wght@300;400;600;700&display=swap">
<style>
  :root {
    --backdrop: #e9e6e1;
    --card-white: #f7f9f8;
    --card-black: #242526;
    --card-black-edge: #2e2f31;
    --gold: #c9a23c;
    --gold-light: #dcb955;
    --ink: #1d1d1d;
    --text-light: #f4f4f4;
    --text-muted: #c9c9c9;
  }
  * { margin: 0; padding: 0; box-sizing: border-box; }
  html, body {
    width: 1200px; height: 863px; overflow: hidden;
    background: var(--backdrop);
    font-family: "Raleway", sans-serif;
  }
  .stage {
    position: relative; width: 1200px; height: 863px;
    display: flex; flex-direction: column; align-items: center; justify-content: center;
    gap: 44px;
  }
  .card {
    position: relative; width: 640px; height: 366px;
    box-shadow: 0 12px 28px rgba(0,0,0,.22);
    overflow: hidden;
  }
  .card--front { background: var(--card-white); }
  .card--back { background: linear-gradient(135deg, var(--card-black-edge), var(--card-black) 60%); }

  .gold-bar {
    position: absolute; width: 9px; height: 92px;
    background: linear-gradient(180deg, var(--gold-light), var(--gold));
  }
  .gold-bar--left-top { left: 0; top: 22px; }
  .gold-bar--right-bottom { right: 0; bottom: 22px; }
  .gold-bar--left-bottom { left: 0; bottom: 22px; }

  .wordmark {
    position: absolute; font-weight: 700; letter-spacing: .02em; white-space: nowrap;
  }
  .card--front .wordmark {
    left: 50%; top: 50%; transform: translate(-50%, -50%);
    font-size: 50px; color: var(--ink);
  }
  .card--back .wordmark {
    right: 46px; bottom: 92px; font-size: 34px; color: var(--text-light);
  }

  .contact-block { position: absolute; left: 46px; top: 46px; color: var(--text-light); }
  .contact-name { font-size: 28px; font-weight: 600; line-height: 1.1; }
  .contact-title { font-size: 12px; font-weight: 600; color: var(--gold-light); margin-top: 3px; }
  .contact-list { list-style: none; margin-top: 14px; }
  .contact-list li {
    display: flex; align-items: center; gap: 10px;
    font-size: 14px; font-weight: 600; margin-bottom: 7px;
  }
  .contact-list svg { width: 14px; height: 14px; flex: none; }
  .tagline {
    margin-top: 14px; font-size: 16px; font-weight: 300; color: var(--text-muted); line-height: 1.3;
  }
</style>
</head>
<body>
<main class="stage">
  <section class="card card--front" aria-label="Card front">
    <span class="gold-bar gold-bar--left-top"></span>
    <span class="gold-bar gold-bar--right-bottom"></span>
    <p class="wordmark">The Loom Briefing</p>
  </section>

  <section class="card card--back" aria-label="Card back">
    <span class="gold-bar gold-bar--left-bottom"></span>
    <span class="gold-bar gold-bar--right-bottom"></span>
    <div class="contact-block">
      <h1 class="contact-name">Belinda Harwick</h1>
      <p class="contact-title">Director and Stylist</p>
      <ul class="contact-list">
        <li>
          <svg viewBox="0 0 16 16" fill="var(--text-light)" aria-hidden="true"><path d="M3.6 1.2l2.2 2.6-1.3 1.7c.9 2 2.4 3.5 4.3 4.4l1.7-1.3 2.6 2.2-1.2 2.5C7 13 3 9 1.1 3.9z"/></svg>
          +61 8 7142 5809
        </li>
        <li>
          <svg viewBox="0 0 16 16" fill="none" stroke="var(--text-light)" stroke-width="1.6" aria-hidden="true"><rect x="1.5" y="3.5" width="13" height="9"/><path d="M1.5 3.5L8 9l6.5-5.5"/></svg>
          belinda@theloombriefing.example
        </li>
        <li>
          <svg viewBox="0 0 16 16" fill="none" stroke="var(--text-light)" stroke-width="1.4" aria-hidden="true"><circle cx="8" cy="8" r="6.5"/><ellipse cx="8" cy="8" rx="2.8" ry="6.5"/><path d="M1.5 8h13"/></svg>
          www.theloombriefing.example
        </li>
      </ul>
      <p class="tagline">Corporate Workwear &amp;<br>Uniform Specialist | Personal Stylist</p>
    </div>
    <p class="wordmark">The Loom Briefing</p>
  </section>
</main>
</body>
</html>
```